Poster Design Project

We are launching a new company Q Vyn, we sell advertising on digital signage and we are launching our company selling ads at our 2 locations, Marlow Bend Sports and Rec Club and the Torrand Isle Sports and Rec Club. We want to advertise that we have 5 10 and 15 ad slots available and ads start from as little as $27.00 per week. We need to let people know we offer 10% discount to WBTGA members. it needs to have the following contact details to get more information, Gideon 0427359042 and gideon@qvyn.com.au. As a new launch we are offering for the first 10 customers one of 2 discounts, get 4 weeks free all you have to pay is the content creation fee ($99 for 5 second ad) or 4 weeks free and free content creation if you sign up to a 18 week contract.

Update: need the add to start wit something like this but you can be creative:

Need to get you message or brand out, Have you heard of digital sinage?
We have ads avaliable starting from $27 per week at one of our locations.

Or something like that, as i am introducing my company they dont know what i do you untill they read this poster.

Target Market(s)

Targeting small to medium buisness

Industry/Entity Type

Advertising

Requirements
Must have
• Logo

```html
<!DOCTYPE html>
<html lang="en">
<head>
<meta charset="utf-8">
<title>Q Vyn – Digital Signage Advertising</title>
<link rel="stylesheet" href="https://fonts.googleapis.com/css2?family=Archivo+Black&family=Dosis:wght@400;500;600;700&display=swap">
<style>
  :root {
    --paper: #ffffff;
    --orange-bright: #f8a800;
    --orange-deep: #d88c00;
    --orange-shadow: #c27c00;
    --charcoal: #474747;
    --ink: #161616;
    --teal: #1a9cbd;
    --lime: #33e02b;
    --brand-blue: #1c8fd6;
    --white: #ffffff;
  }
  html, body {
    margin: 0;
    padding: 0;
    overflow: hidden;
    background: var(--paper);
  }
  .poster {
    position: relative;
    width: 848px;
    height: 1200px;
    overflow: hidden;
    background: var(--paper);
    font-family: "Dosis", "Trebuchet MS", sans-serif;
  }
  .backdrop {
    position: absolute;
    inset: 0;
    width: 848px;
    height: 1200px;
  }
  .brand {
    position: absolute;
    left: 74px;
    top: 120px;
    display: flex;
    align-items: center;
    gap: 22px;
  }
  .brand-square {
    width: 84px;
    height: 84px;
    background: var(--brand-blue);
  }
  .brand-name {
    font-family: "Archivo Black", "Arial Black", sans-serif;
    font-size: 80px;
    line-height: 1;
    color: var(--ink);
  }
  .hook {
    position: absolute;
    left: 74px;
    top: 248px;
    width: 520px;
    margin: 0;
    color: var(--ink);
  }
  .hook-question {
    margin: 0;
    font-size: 30px;
    font-weight: 700;
    line-height: 38px;
  }
  .hook-locations {
    margin: 14px 0 0;
    font-size: 22px;
    font-weight: 500;
    line-height: 28px;
    width: 440px;
  }
  .offer {
    position: absolute;
    left: 72px;
    top: 466px;
    width: 720px;
    margin: 0;
    font-size: 39px;
    font-weight: 600;
    line-height: 48px;
    color: var(--ink);
  }
  .offer-strong {
    font-family: "Archivo Black", "Arial Black", sans-serif;
    font-weight: 400;
    font-size: 36px;
    text-shadow: 1px 2px 3px rgba(0,0,0,0.35);
  }
  .offer-price {
    font-family: "Archivo Black", "Arial Black", sans-serif;
    font-weight: 400;
    font-size: 40px;
    color: var(--lime);
    text-shadow: 1px 2px 3px rgba(0,0,0,0.45);
  }
  .discount {
    position: absolute;
    left: 0;
    top: 0;
    width: 848px;
    height: 1200px;
  }
  .discount text {
    font-family: "Archivo Black", "Arial Black", sans-serif;
    font-size: 82px;
  }
  .discount .teal { fill: var(--teal); }
  .discount .ink { fill: var(--ink); }
  .launch {
    position: absolute;
    left: 40px;
    top: 930px;
    width: 300px;
    margin: 0;
    color: var(--ink);
  }
  .launch-title {
    margin: 0 0 6px;
    font-size: 23px;
    font-weight: 700;
    line-height: 28px;
  }
  .launch-list {
    margin: 0;
    padding: 0;
    list-style: none;
    font-size: 19px;
    font-weight: 600;
    line-height: 24px;
  }
  .launch-list li + li {
    margin-top: 6px;
  }
  .contact {
    position: absolute;
    right: 52px;
    top: 1032px;
    margin: 0;
    text-align: right;
    font-size: 28px;
    font-weight: 500;
    line-height: 38px;
    color: var(--white);
    font-style: normal;
  }
</style>
</head>
<body>
<main class="poster">
  <svg class="backdrop" viewBox="0 0 707 1000" preserveAspectRatio="none" aria-hidden="true">
    <defs>
      <filter id="panel-shadow" x="-20%" y="-20%" width="140%" height="140%">
        <feDropShadow dx="-6" dy="4" stdDeviation="8" flood-color="#000" flood-opacity="0.35"/>
      </filter>
      <linearGradient id="middle-fold" x1="1" y1="0" x2="0.3" y2="1">
        <stop offset="0" stop-color="var(--orange-bright)"/>
        <stop offset="0.45" stop-color="var(--orange-bright)"/>
        <stop offset="0.75" stop-color="var(--orange-deep)"/>
        <stop offset="1" stop-color="var(--orange-shadow)"/>
      </linearGradient>
    </defs>
    <polygon class="fold-middle" points="707,0 707,1000 330,1000 120,640" fill="url(#middle-fold)" filter="url(#panel-shadow)"/>
    <polygon class="fold-left" points="0,430 340,1000 0,1000" fill="var(--orange-bright)" filter="url(#panel-shadow)"/>
    <polygon class="fold-corner" points="707,752 707,1000 335,1000 300,936" fill="var(--charcoal)" filter="url(#panel-shadow)"/>
  </svg>

  <header class="brand">
    <div class="brand-square"></div>
    <span class="brand-name">Q Vyn</span>
  </header>

  <section class="hook">
    <p class="hook-question">Need to get your message or brand out?<br>Have you heard of digital signage?</p>
    <p class="hook-locations">Our screens are at Marlow Bend Sports and Rec Club and Torrand Isle Sports and Rec Club.</p>
  </section>

  <p class="offer">
    5 10 and 15 ad <span class="offer-strong">slots available</span> and<br>
    ads start from as little as<br>
    <span class="offer-price">$27.00</span> per week
  </p>

  <svg class="discount" viewBox="0 0 848 1200" aria-label="10% discount to WBTGA members">
    <defs>
      <filter id="type-shadow" x="-5%" y="-20%" width="110%" height="150%">
        <feDropShadow dx="2" dy="3" stdDeviation="3" flood-color="#000" flood-opacity="0.4"/>
      </filter>
    </defs>
    <text x="94" y="806" textLength="668" lengthAdjust="spacingAndGlyphs" filter="url(#type-shadow)"><tspan class="teal">10% discount</tspan><tspan class="ink"> to</tspan></text>
    <text class="ink" x="94" y="884" textLength="668" lengthAdjust="spacingAndGlyphs" filter="url(#type-shadow)">WBTGA members</text>
  </svg>

  <section class="launch">
    <p class="launch-title">Launch offer – first 10 customers:</p>
    <ul class="launch-list">
      <li>4 weeks free – just pay the content fee ($99 for a 5 second ad)</li>
      <li>or 4 weeks free plus free content on an 18 week contract</li>
    </ul>
  </section>

  <address class="contact">
    Gideon<br>
    0427359042<br>
    gideon@qvyn.com.au
  </address>
</main>
</body>
</html>
```